To design a brand identity that is simple and creative with 'Corvane' as the brand name, I like modern simple fonts like helvetica neue, I want to print both sides of the card, I am open to dark front and white back, but the design needs to transfer well to letter heads and email signatures, I am looking for sophisticated and elegant, but open minded about clever and off the wall, I do not do 'boring' Corvane Ventures is the mother company for a small group, specialising in Management & consulting, Software development and construction, we have a high level of integrity, we are transparent and accountable for what we do. my images are provided as a guide only, Im not expecting them to be just copied, Im looking for a creator and passionate thinker, who will put life into their work.

Target Market(s)

usually business minded people who are looking for something different in me, such as leadership, confidence and focus with thinking that is per haps a little outside the box..

Industry/Entity Type

Construction

Requirements
Must have
• clean, minmalistic
Nice to have
• custom logo
Should not have
• boring, traditional

```html
<!DOCTYPE html>
<html lang="en">
<head>
<meta charset="utf-8">
<title>Corvane Ventures – Business Card</title>
<link rel="stylesheet" href="https://fonts.googleapis.com/css2?family=Questrial&family=Caveat:wght@400&display=swap">
<style>
  :root {
    --stage: #34302e;
    --card-light: #f4f4f4;
    --card-light-shade: #e6e6e6;
    --card-dark: #1d1d1d;
    --ink: #1c1c1c;
    --ink-soft: #555555;
    --ghost: rgba(0, 0, 0, 0.16);
    --accent: #e0301e;
    --accent-warm: #ea5a2a;
    --paper-white: #ffffff;
    --label: #c9c6c3;
  }
  html, body {
    margin: 0;
    padding: 0;
    width: 1200px;
    height: 1000px;
    overflow: hidden;
    background: var(--stage);
    font-family: "Questrial", "Helvetica Neue", Arial, sans-serif;
  }
  .canvas {
    position: relative;
    width: 1200px;
    height: 1000px;
  }

  /* ---------- Front card (portrait) ---------- */
  .card-front {
    position: absolute;
    left: 60px;
    top: 150px;
    width: 420px;
    height: 700px;
    color: var(--ink);
    overflow: hidden;
  }
  .front-texture {
    position: absolute;
    inset: 0;
    background: linear-gradient(135deg, #fafafa 0%, #ececec 100%);
  }
  .front-brand {
    position: absolute;
    top: 56px;
    right: 40px;
    display: flex;
    align-items: center;
    gap: 16px;
  }
  .brand-dot {
    width: 44px;
    height: 44px;
    border-radius: 50%;
    background: var(--accent-warm);
  }
  .front-brand .brand-name {
    font-size: 58px;
    line-height: 1;
    letter-spacing: 1px;
    color: var(--ink);
  }
  .front-tagline {
    position: absolute;
    top: 128px;
    right: 40px;
    font-family: "Caveat", cursive;
    font-size: 21px;
    line-height: 1;
    color: var(--ink);
    transform: rotate(-3deg);
  }
  .front-web {
    position: absolute;
    top: 158px;
    right: 40px;
    font-size: 18px;
    line-height: 1;
    letter-spacing: 0.5px;
    color: var(--ink-soft);
  }
  .front-web .web-prefix { color: var(--accent-warm); }
  .front-motto {
    position: absolute;
    top: 212px;
    right: 48px;
    font-family: "Caveat", cursive;
    font-size: 28px;
    line-height: 1;
    transform: rotate(-6deg);
  }
  .front-ghost-name {
    position: absolute;
    left: 252px;
    top: 250px;
    transform-origin: left top;
    transform: rotate(90deg);
    font-size: 76px;
    line-height: 1;
    color: var(--ghost);
    letter-spacing: 2px;
    white-space: nowrap;
  }
  .front-services {
    position: absolute;
    left: 212px;
    top: 200px;
    transform-origin: left top;
    transform: rotate(90deg);
    font-size: 16px;
    line-height: 1;
    letter-spacing: 0.5px;
    white-space: nowrap;
  }
  .service-sep { color: var(--accent); padding: 0 5px; }
  .front-contact {
    position: absolute;
    right: 40px;
    bottom: 52px;
    text-align: right;
  }
  .contact-name {
    font-size: 30px;
    line-height: 1;
    margin-bottom: 18px;
  }
  .contact-line {
    display: flex;
    justify-content: flex-end;
    align-items: center;
    gap: 8px;
    font-size: 16px;
    line-height: 1.2;
    margin-top: 8px;
  }
  .contact-line svg { width: 16px; height: 16px; }
  .icon-phone { fill: var(--accent); }

  /* ---------- Back card (landscape) ---------- */
  .card-back {
    position: absolute;
    left: 540px;
    top: 300px;
    width: 620px;
    height: 400px;
    background: var(--card-dark);
    overflow: hidden;
    color: var(--paper-white);
  }
  .back-photo {
    position: absolute;
    inset: 0;
    background: radial-gradient(ellipse at 35% 50%, #9a9a9a 0%, #5e5e5e 40%, #262626 75%, var(--card-dark) 100%);
  }
  .back-brand {
    position: absolute;
    left: 40px;
    top: 112px;
    display: flex;
    align-items: center;
    gap: 22px;
  }
  .back-brand .brand-dot {
    width: 96px;
    height: 96px;
  }
  .back-brand .brand-name {
    font-size: 100px;
    line-height: 1;
    color: var(--paper-white);
  }
  .back-services {
    position: absolute;
    left: 52px;
    top: 250px;
    font-size: 19px;
    line-height: 1;
    letter-spacing: 2px;
    color: var(--paper-white);
  }

  .side-label {
    position: absolute;
    font-size: 20px;
    line-height: 1;
    color: var(--label);
  }
  .label-front { left: 124px; top: 870px; }
  .label-back { left: 1036px; top: 720px; }
</style>
</head>
<body>
<main class="canvas">

  <section class="card-front" aria-label="Card front">
    <div class="front-texture" role="img" aria-label="Soft white embossed cube pattern"></div>

    <div class="front-brand">
      <span class="brand-dot"></span>
      <span class="brand-name">corvane</span>
    </div>
    <div class="front-tagline">... in the creation business</div>
    <div class="front-web"><span class="web-prefix">www.</span> corvane.ventures</div>
    <div class="front-motto">‘pure passion’</div>

    <div class="front-ghost-name" aria-hidden="true">corvane</div>
    <div class="front-services">management<span class="service-sep">•</span>software<span class="service-sep">•</span>construction</div>

    <div class="front-contact">
      <div class="contact-name">milo</div>
      <div class="contact-line">+ 61 0400 555 012
        <svg viewBox="0 0 24 24" aria-hidden="true"><path class="icon-phone" d="M6.6 10.8a15.1 15.1 0 0 0 6.6 6.6l2.2-2.2a1 1 0 0 1 1-.25 11.4 11.4 0 0 0 3.6.57 1 1 0 0 1 1 1V20a1 1 0 0 1-1 1A17 17 0 0 1 3 4a1 1 0 0 1 1-1h3.5a1 1 0 0 1 1 1 11.4 11.4 0 0 0 .57 3.6 1 1 0 0 1-.25 1z"/></svg>
      </div>
      <div class="contact-line">milo@corvane.ventures
        <svg viewBox="0 0 24 24" aria-hidden="true"><rect x="2" y="5" width="20" height="14" fill="#e0301e"/><path d="M3 6l9 7 9-7" fill="none" stroke="#ffffff" stroke-width="1.6"/></svg>
      </div>
    </div>
  </section>

  <section class="card-back" aria-label="Card back">
    <div class="back-photo" role="img" aria-label="Black and white photo of an ice cliff with a small boat at its base"></div>
    <div class="back-brand">
      <span class="brand-dot"></span>
      <span class="brand-name">corvane</span>
    </div>
    <div class="back-services">management<span class="service-sep">•</span>software<span class="service-sep">•</span>construction</div>
  </section>

  <div class="side-label label-front">Front</div>
  <div class="side-label label-back">Back</div>

</main>
</body>
</html>
```